Business Card Design for Occupational Medicine Start Up Company

We need to design a professional business card. We are a healthcare company providing occupational medicine services to blue collar industries. We are professional, efficient and high quality service providers.

Target Market(s)

Blue Collar Industry: Shipbuilding, Ports, Trucking Companies; The Executives and Safety Officers for these companies

Industry/Entity Type

Healthcare

Contact Information for Business Card

Logo, Name, Title, Email, Phone

Other font styles liked:
• Please match our Brand Guide

Requirements
Must have
• Our Company Colors and Logo

```html
<!DOCTYPE html>
<html lang="en">
<head>
<meta charset="UTF-8">
<title>CrewWell Clinics – Business Card</title>
<link href="https://fonts.googleapis.com/css2?family=Montserrat:wght@400;500;600&display=swap" rel="stylesheet">
<style>
  :root {
    --navy: #2f3079;
    --sky: #2f9fd8;
    --amber: #f0ac3c;
    --paper: #f7f7f5;
    --page: #2a2a2a;
    --white: #ffffff;
  }
  * { margin: 0; padding: 0; box-sizing: border-box; }
  html, body {
    width: 1200px; height: 1200px; overflow: hidden;
    background: var(--page);
    font-family: "Montserrat", sans-serif;
  }
  .canvas { position: relative; width: 1200px; height: 1200px; }
  .card {
    position: absolute; left: 303px; width: 594px; height: 348px;
    border-radius: 22px; overflow: hidden;
  }
  .card--front { top: 200px; background: var(--navy); }
  .card--back { top: 640px; background: var(--paper); }

  .brand-mark {
    position: absolute; border-radius: 50%;
  }
  .card--front .brand-mark {
    left: 255px; top: 28px; width: 300px; height: 300px; background: var(--sky);
  }
  .card--back .brand-mark {
    left: 305px; top: 25px; width: 300px; height: 300px; background: var(--sky);
  }

  .wordmark {
    position: absolute; font-weight: 600; line-height: 1; text-align: center;
  }
  .wordmark__name { display: block; font-size: 27px; letter-spacing: 0.5px; }
  .wordmark__sub { display: block; font-size: 15px; letter-spacing: 4px; margin-top: 6px; }
  .card--front .wordmark { left: 29px; top: 256px; color: var(--white); width: 262px; }
  .card--back .wordmark { left: 26px; top: 43px; color: var(--navy); width: 236px; }
  .card--back .wordmark__name { font-size: 24px; }
  .card--back .wordmark__sub { font-size: 13px; }

  .person { position: absolute; left: 26px; top: 140px; }
  .person__name { font-size: 23px; font-weight: 600; color: var(--sky); letter-spacing: 0.5px; }
  .person__title { font-size: 15px; font-weight: 400; color: var(--navy); margin-top: 4px; }

  .address {
    position: absolute; left: 26px; top: 210px; font-style: normal;
    font-size: 15px; line-height: 21px; color: var(--navy);
  }
  .contacts { position: absolute; left: 26px; top: 262px; list-style: none; }
  .contacts li {
    display: flex; align-items: center; height: 21px;
    font-size: 15px; color: var(--navy);
  }
  .contacts svg { width: 13px; height: 13px; margin: 0 14px 0 4px; flex: none; }
</style>
</head>
<body>
<main class="canvas">
  <section class="card card--front" aria-label="Card front">
    <div class="brand-mark" aria-hidden="true"></div>
    <div class="wordmark">
      <span class="wordmark__name">CREWWELL</span>
      <span class="wordmark__sub">CLINICS</span>
    </div>
  </section>

  <section class="card card--back" aria-label="Card back">
    <div class="brand-mark" aria-hidden="true"></div>
    <div class="wordmark">
      <span class="wordmark__name">CREWWELL</span>
      <span class="wordmark__sub">CLINICS</span>
    </div>
    <div class="person">
      <p class="person__name">DANIEL REYES</p>
      <p class="person__title">Senior Doctor</p>
    </div>
    <address class="address">
      48 Harbor Avenue, Suite 210<br>
      Bayport, State 54321
    </address>
    <ul class="contacts">
      <li>
        <svg viewBox="0 0 16 16" aria-hidden="true"><path fill="#2f9fd8" d="M2 5c0-2 2-3 6-3s6 1 6 3v1h-3V4.5H5V6H2z"/><rect x="3" y="8" width="10" height="6" rx="1" fill="#2f9fd8"/></svg>
        555-210-4387
      </li>
      <li>
        <svg viewBox="0 0 16 16" aria-hidden="true"><rect x="1" y="3" width="14" height="10" fill="#2f3079"/><path d="M1.5 3.5 8 9l6.5-5.5" fill="none" stroke="#f7f7f5" stroke-width="1.4"/></svg>
        daniel@crewwellclinics.com
      </li>
      <li>
        <svg viewBox="0 0 16 16" aria-hidden="true"><circle cx="8" cy="8" r="7" fill="#f0ac3c"/><path d="M1 8h14M8 1v14M3 4.5h10M3 11.5h10" stroke="#f7f7f5" stroke-width="0.9" fill="none"/></svg>
        www.crewwellclinics.com
      </li>
    </ul>
  </section>
</main>
</body>
</html>
```